Business Card Design

Business Card for professional consulting firm working with large financial institutions.

Target Market(s)

Executive buyers

Industry/Entity Type

Banking

Contact Information for Business Card

Mild creativity wanted. Not boring, but do elaborate artwork.

Font styles to use
Serif
Sans Serif

Colors

Designer to choose colors to be used in the design.

Requirements
Must have
• Standard business card features - company name, individual name, telephone, website, email, locations.
Nice to have
• Two colors
Should not have
• too many colors, fancy printing, cartoons.

```html
<!DOCTYPE html>
<html lang="en">
<head>
<meta charset="utf-8">
<title>Halbrook Group – Business Card</title>
<link href="https://fonts.googleapis.com/css2?family=Alegreya:wght@400&family=Montserrat:wght@500;600&family=Roboto:wght@400&display=swap" rel="stylesheet">
<style>
  :root {
    --stage: #6b4e36;
    --ink: #000000;
    --paper: #f4f4f4;
    --swoosh: #c6c6c6;
    --text-dark: #2e2e2e;
    --text-light: #ffffff;
  }
  * { margin: 0; padding: 0; box-sizing: border-box; }
  html, body { width: 1200px; height: 960px; overflow: hidden; }
  body { background: var(--stage); position: relative; }

  .card {
    position: absolute;
    width: 600px;
    height: 342px;
    background: var(--ink);
    overflow: hidden;
    box-shadow: 0 3px 8px rgba(0,0,0,0.45);
  }
  .card--front { left: 322px; top: 109px; }
  .card--back  { left: 320px; top: 494px; }

  .card__shape { position: absolute; inset: 0; }

  .holder {
    position: absolute;
    right: 32px;
    top: 20px;
    text-align: right;
    color: var(--text-light);
    font-family: "Montserrat", sans-serif;
  }
  .holder__name { font-size: 20px; font-weight: 500; letter-spacing: 0.2px; line-height: 26px; }
  .holder__role { font-size: 13px; font-weight: 600; line-height: 16px; }

  .wordmark {
    position: absolute;
    font-family: "Alegreya", serif;
    font-weight: 400;
    white-space: nowrap;
  }
  .card--front .wordmark {
    left: 48px; top: 142px;
    font-size: 28px;
    color: var(--text-dark);
  }
  .card--back .wordmark {
    left: 0; right: 0; top: 132px;
    text-align: center;
    font-size: 46px;
    color: var(--text-light);
  }

  .contact, .address {
    position: absolute;
    bottom: 24px;
    font-family: "Roboto", sans-serif;
    font-size: 14px;
    line-height: 19px;
    color: var(--text-dark);
  }
  .contact { left: 32px; list-style: none; }
  .contact li { display: flex; align-items: center; gap: 7px; }
  .contact svg { width: 13px; height: 13px; fill: var(--text-dark); flex: none; }
  .address { right: 32px; text-align: right; font-style: normal; }
</style>
</head>
<body>

<section class="card card--front" aria-label="Business card front">
  <svg class="card__shape" viewBox="0 0 600 342" aria-hidden="true">
    <path fill="var(--swoosh)" d="M0,342 L0,66 C20,8 90,2 150,4 C300,10 470,90 600,182 L600,342 Z"/>
    <path fill="var(--paper)" d="M0,342 L0,82 C25,22 95,18 150,22 C300,34 470,125 600,226 L600,342 Z"/>
  </svg>

  <div class="holder">
    <p class="holder__name">DANIEL REYES</p>
    <p class="holder__role">CEO/FOUNDER</p>
  </div>

  <p class="wordmark">Halbrook Group</p>

  <ul class="contact">
    <li>
      <svg viewBox="0 0 24 24"><path d="M6.6 10.8c1.4 2.8 3.8 5.1 6.6 6.6l2.2-2.2c.3-.3.7-.4 1-.2 1.1.4 2.3.6 3.6.6.6 0 1 .4 1 1V20c0 .6-.4 1-1 1C10.6 21 3 13.4 3 4c0-.6.4-1 1-1h3.5c.6 0 1 .4 1 1 0 1.3.2 2.5.6 3.6.1.3 0 .7-.2 1z"/></svg>
      555 210 4817
    </li>
    <li>
      <svg viewBox="0 0 24 24"><path d="M2 5h20v2l-10 6L2 7zM2 9l10 6 10-6v10H2z"/></svg>
      info@halbrookgroup.com
    </li>
    <li>
      <svg viewBox="0 0 24 24"><circle cx="12" cy="12" r="10"/></svg>
      www.halbrookgroup.com
    </li>
  </ul>

  <address class="address">
    Halbrook Group<br>
    1420 Harbor View Road<br>
    Juneau, Alaska 99801
  </address>
</section>

<section class="card card--back" aria-label="Business card back">
  <p class="wordmark">Halbrook Group</p>
</section>

</body>
</html>
```